Stationery Design Project for Nimbora, Chicago

Nimbora, a street parking application which helps car drivers find a street parking spot by offering an ideal path along which to look for parking. This path is calculated by our algorithm based on data (e.g. historical data, baseball games schedule, etc.). Along this path the driver will find a spot and will also save 70% of the search time. Customer we target is reg. between 21 and 45 yo.

We envision something young, fresh, bright and original. Slightly abstract maybe. It should represent the idea and elements of finding street parking in the city, e.g. car(s), parking spot, people, city, etc. (just ideas!).

Logo is attached.

Requirement:
- Business Cards (2 Sided Full Color CMYK)
- Letterhead (1 Sided Full Color CMYK)
- Envelope (1 Sided Full Color CMYK)
- Sticker (1 Sided Full Color CMYK), round with a 2inch diameter.

Reason: We're starting to get more and more designs and need more time to look into all of them. Very exciting!! Thanks to everybody!

Hi all, we're in the process of selecting our favs. Though choices!!! Really good submissions. Will keep you posted and sorry for the delay.

Target Market(s)

Car drivers and owners between 21 and 45

Industry/Entity Type

Parking

Requirements
Must have
• Sticker should be round and include company URL nimbora.com and the new logo which we will attach soon.
Should not have
• Should not be too serious or boring.

```html
<!DOCTYPE html>
<html lang="en">
<head>
<meta charset="utf-8">
<title>Nimbora Business Card</title>
<link href="https://fonts.googleapis.com/css2?family=Open+Sans:wght@400;600;700&display=swap" rel="stylesheet">
<style>
  :root {
    --backdrop: #e4e4e4;
    --card-light: #ffffff;
    --card-dark: #58585a;
    --card-dark-core: #050505;
    --ink: #1f1f1f;
    --ink-soft: #555555;
    --ink-body: #444444;
    --brand-blue: #1877c4;
    --brand-blue-deep: #1f3fa8;
    --white: #ffffff;
  }
  html, body {
    margin: 0;
    padding: 0;
    width: 1200px;
    height: 954px;
    overflow: hidden;
    background: var(--backdrop);
    font-family: "Open Sans", Arial, sans-serif;
  }
  .canvas {
    position: relative;
    width: 1200px;
    height: 954px;
  }
  .card {
    position: absolute;
    top: 77px;
    width: 454px;
    height: 795px;
    border-radius: 28px;
    overflow: hidden;
    box-shadow: 0 6px 14px rgba(0,0,0,0.25);
  }
  .card--front { left: 79px; background: var(--card-light); }
  .card--back {
    left: 633px;
    background: radial-gradient(ellipse 60% 45% at 45% 55%, var(--card-dark-core) 0%, #1a1a1a 55%, var(--card-dark) 100%);
  }
  .brand-dot {
    position: absolute;
    left: 152px;
    top: 55px;
    width: 150px;
    height: 150px;
    border-radius: 50%;
    background: var(--brand-blue-deep);
  }
  .card--back .brand-dot { left: 154px; top: 72px; }
  .wordmark {
    position: absolute;
    left: 0;
    width: 100%;
    text-align: center;
    font-size: 92px;
    font-weight: 600;
    line-height: 1;
    letter-spacing: 1px;
  }
  .card--front .wordmark { top: 222px; color: var(--ink); }
  .card--back .wordmark { top: 240px; color: var(--white); }
  .identity {
    position: absolute;
    left: 49px;
    top: 350px;
    color: var(--ink-soft);
    white-space: nowrap;
  }
  .identity__name { font-size: 33px; font-weight: 700; }
  .identity__role { font-size: 23px; font-weight: 400; }
  .contact {
    position: absolute;
    left: 38px;
    top: 580px;
    margin: 0;
    padding: 0;
    list-style: none;
    font-size: 19.5px;
    line-height: 26.7px;
    color: var(--ink-body);
  }
  .contact b { font-weight: 700; }
  .address {
    position: absolute;
    left: 38px;
    top: 713px;
    margin: 0;
    font-size: 19.5px;
    line-height: 26.5px;
    color: var(--ink-body);
  }
  .web {
    position: absolute;
    left: 45px;
    top: 718px;
    font-size: 27px;
    color: var(--white);
  }
  .accent-band {
    position: absolute;
    right: 0;
    bottom: 0;
    width: 180px;
    height: 400px;
  }
</style>
</head>
<body>
<div class="canvas">

  <section class="card card--front">
    <div class="brand-dot"></div>
    <div class="wordmark">nimbora</div>
    <div class="identity">
      <span class="identity__name">Your Name</span>
      <span class="identity__role"> | Designation</span>
    </div>
    <ul class="contact">
      <li><b>p</b> : 123-456-7890</li>
      <li><b>c</b> : 123-456-7890</li>
      <li><b>e</b> : name@website.com</li>
      <li><b>w</b> : www.website.com</li>
    </ul>
    <p class="address">City Name, Street Name,<br>State Name, Country Code</p>
    <svg class="accent-band" viewBox="0 0 180 400" aria-hidden="true">
      <defs>
        <linearGradient id="bandFront" x1="0" y1="0" x2="0" y2="1">
          <stop offset="0" stop-color="#1877c4"/>
          <stop offset="1" stop-color="#1f3fa8"/>
        </linearGradient>
      </defs>
      <polygon points="100,0 180,0 180,400 0,400" fill="url(#bandFront)"/>
    </svg>
  </section>

  <section class="card card--back">
    <div class="brand-dot"></div>
    <div class="wordmark">nimbora</div>
    <div class="web">www.website.com</div>
    <svg class="accent-band" viewBox="0 0 180 400" aria-hidden="true">
      <defs>
        <linearGradient id="bandBack" x1="0" y1="0" x2="0" y2="1">
          <stop offset="0" stop-color="#1877c4"/>
          <stop offset="1" stop-color="#1f3fa8"/>
        </linearGradient>
      </defs>
      <polygon points="100,0 180,0 180,400 0,400" fill="url(#bandBack)"/>
    </svg>
  </section>

</div>
</body>
</html>
```